KTWG application splash screen

We need a 1024x768 image for use as an application splash screen.
The image will be displayed full screen on an 10 inch industrial PC 1024x768 screen while our application is launching. The image should convey that the application is "Waiting for connection to Wi-Fi access point..." and include a graphic of the industrial PC connected to the access point via an Ethernet cable. A list of troubleshooting steps should be included at the bottom of the image. The troubleshooting steps should not be the main focus of the image and should be shown in a smaller font (but still readable at 1024x768 displayed on a 10 inch screen).
I will include a mock up of the general idea of what we are looking for as well as image files for the industrial PC, a screenshot of our application to show on the PC's screen and the AP.
For general look and feel and a sense of corporate branding please review our website https://marrowgatesoilworks.example/. The splash screen should reflect corporate branding.
Target Market(s)
Users of our application
Industry/Entity Type
Agriculture
Look and feel

```html
<!DOCTYPE html>
<html lang="en">
<head>
<meta charset="utf-8">
<title>KTWG – Waiting for Wi-Fi access point</title>
<link rel="stylesheet" href="https://fonts.googleapis.com/css2?family=Barlow:wght@400;500;600&family=Lato:wght@400;700&display=swap">
<style>
  :root {
    --brand-green: #2bb673;
    --paper: #ffffff;
    --ink: #1c1c1c;
    --device-dark: #2b2b2b;
    --device-mid: #4a4a4a;
    --ap-light: #f4f4f4;
    --ap-shade: #d9d9d9;
  }
  html, body {
    margin: 0;
    padding: 0;
    width: 1200px;
    height: 900px;
    overflow: hidden;
    background: var(--paper);
  }
  .canvas {
    position: relative;
    width: 1200px;
    height: 900px;
    overflow: hidden;
    background: var(--paper);
  }
  .splash {
    position: absolute;
    top: 0;
    left: 0;
    width: 1024px;
    height: 768px;
    transform: scale(1.171875);
    transform-origin: 0 0;
    font-family: "Barlow", sans-serif;
  }
  .backdrop {
    position: absolute;
    inset: 0;
    width: 1024px;
    height: 768px;
  }
  .headline {
    position: absolute;
    top: 26px;
    left: 20px;
    width: 650px;
    margin: 0;
    text-align: center;
    color: var(--paper);
    font-weight: 500;
    font-size: 63px;
    line-height: 72px;
    letter-spacing: 0.5px;
  }
  .device-computer {
    position: absolute;
    left: 86px;
    top: 326px;
    width: 272px;
    height: 220px;
    border-radius: 14px;
    background: linear-gradient(180deg, var(--device-mid), var(--device-dark));
  }
  .device-access-point {
    position: absolute;
    left: 862px;
    top: 122px;
    width: 54px;
    height: 344px;
    border-radius: 10px;
    background: linear-gradient(90deg, var(--ap-shade), var(--ap-light) 45%, var(--ap-shade));
  }
  .label-computer {
    position: absolute;
    left: 60px;
    top: 553px;
    width: 320px;
    text-align: center;
    color: var(--brand-green);
    font-size: 24px;
    font-weight: 400;
    margin: 0;
  }
  .label-access-point {
    position: absolute;
    left: 805px;
    top: 524px;
    width: 155px;
    text-align: center;
    color: var(--paper);
    font-size: 17px;
    line-height: 21px;
    font-weight: 500;
    letter-spacing: 0.5px;
    margin: 0;
  }
  .troubleshooting {
    position: absolute;
    left: 48px;
    top: 626px;
    width: 690px;
    color: var(--paper);
    font-family: "Lato", sans-serif;
  }
  .troubleshooting-title {
    margin: 0 0 8px;
    font-size: 12px;
    font-weight: 700;
  }
  .step-list, .sub-step-list {
    list-style: none;
    margin: 0;
    padding: 0;
  }
  .step-list > li {
    position: relative;
    padding-left: 17px;
    font-size: 11.3px;
    line-height: 16px;
  }
  .step-list > li::before {
    content: "➤";
    position: absolute;
    left: 0;
    font-size: 11px;
  }
  .sub-step-list > li {
    position: relative;
    padding-left: 20px;
    margin-left: 5px;
  }
  .sub-step-list > li::before {
    content: "➜";
    position: absolute;
    left: 2px;
    font-size: 10px;
  }
  .brand-tile {
    position: absolute;
    left: 808px;
    top: 596px;
    width: 147px;
    height: 147px;
    border-radius: 32px;
    background: var(--brand-green);
    display: flex;
    align-items: center;
    justify-content: center;
  }
  .brand-name {
    color: var(--paper);
    font-family: "Barlow", sans-serif;
    font-weight: 600;
    font-size: 40px;
    letter-spacing: 1px;
  }
</style>
</head>
<body>
<div class="canvas">
  <div class="splash">
    <svg class="backdrop" viewBox="0 0 1024 768" xmlns="http://www.w3.org/2000/svg" aria-hidden="true">
      <!-- header band with sweeping lobe -->
      <path d="M0 0 H1024 V100 H790 C720 100 700 160 655 210 C615 252 585 268 545 268 H0 Z" fill="var(--brand-green)"/>
      <!-- access point column -->
      <path d="M805 160 Q805 100 865 100 H960 V640 H805 Z" fill="var(--brand-green)"/>
      <!-- brand tile frame -->
      <rect x="790" y="580" width="182" height="200" rx="44" fill="var(--paper)"/>
      <!-- troubleshooting panel with tab -->
      <path d="M0 612 H185 L210 637 H740 V768 H0 Z" fill="var(--brand-green)"/>
      <!-- ethernet cable -->
      <path d="M356 505 H862 Q886 505 886 482 V462" fill="none" stroke="var(--ink)" stroke-width="5" stroke-linecap="round"/>
    </svg>

    <h1 class="headline">Waiting for<br>connection to Wi-Fi<br>access point...</h1>

    <div class="device-computer" role="img" aria-label="Rugged tractor cab computer showing the KTWG seeding application"></div>
    <p class="label-computer">Tractor Cab Computer</p>

    <div class="device-access-point" role="img" aria-label="Outdoor Wi-Fi access point with two antennas"></div>
    <p class="label-access-point">Wi-Fi Access<br>Point</p>

    <section class="troubleshooting">
      <h2 class="troubleshooting-title">Troubleshooting steps:</h2>
      <ul class="step-list">
        <li>This screen should only be visible for a short time on boot.</li>
        <li>If this screen stays visible for more than a minute:
          <ul class="sub-step-list">
            <li>Verify that the Wi-Fi Access Point (AP) powers up when this system does (indicated by a green light on the side of the AP).</li>
            <li>Check the Ethernet cable between this system and the AP for damage, and replace it if necessary.</li>
            <li>Power-cycle this system and wait for it to reboot fully.</li>
            <li>If the issue persists, contact KTWG support for further assistance.</li>
          </ul>
        </li>
      </ul>
    </section>

    <div class="brand-tile">
      <span class="brand-name">KTWG</span>
    </div>
  </div>
</div>
</body>
</html>
```